A4 Single Page Brochure for Private Cloud Offerings

Theme: Futuristic Tech Company

Meridane Systems is looking to offer private cloud services for our enterprise customers in Perth-based data-centres that provides our clients with a lower-cost alternative to Kelvara or QNL yielding better performance.

We are looking for a single A4 brochure with a great graphics design theme to promote these services.

We will be providing five tiers:
- Starter
- Growth
- Professional
- Premier
- Elite

Each plan must list on the brochure the Max VMs, CPU cores, Memory and SSD storage allocated. Refer to the uploaded PNG file.

The brochure must list the following selling points:

- Hosted in a local Perth-based TIER3 and TIER4 datacentres
- WA owned hosting - support local
- Low latency - ultra fast local hosting
- Includes Orvix Host Datacentre licensing
- Includes BrakWall Managed Firewalls for Enterprise level threat detection
- Includes all infrastructure maintenance services
- Full self management of VMs through customer portal
- Includes a 1gbps Internet link
- Predictable fixed monthly fee with no dynamic billing
- No additional charges for Storage Transactions, Internet Usage, VM Snapshots, Datacentre Bandwidth Usage and Firewall Traffic Usage.
- Highly available cluster, no single point of failure.
- Pricing is based on 36 months commit
- Yearly rate increases capped to a maximum of Australian CPI
- All plans have 24/7/365 support with dedicated after hours number.
- Managed backup and managed disaster recovery services can be added to plans

Service provided in accordance with our terms and conditions.

We need the ability to EDIT the brochure to adjust pricing after we receive the final project.

I have uploaded more details on these plans under the attachment PrivateCloudPlans.png.

Please do not utilise "Pushing the Boundaries of Technology" - our brand is being replaced with "Specialised Consulting". New website is under development but not launched yet.

Target Market(s)

Information Technology Sector

Colors
0054AA
0677BA
7BADD7
CADEEF
E8F1F8

Requirements
Must have
• Theme of Meridane is Blue
Should not have
• Extremely stock imagary that just looks "cheap and stock"

```html
<!DOCTYPE html>
<html lang="en">
<head>
<meta charset="utf-8">
<title>Meridane Systems – Private Cloud Services</title>
<link href="https://fonts.googleapis.com/css2?family=Orbitron:wght@700;900&family=Poppins:wght@400;500;600;700&family=Montserrat:wght@800&family=Oswald:wght@600&display=swap" rel="stylesheet">
<style>
  :root {
    --navy: #1b2a7a;
    --brand: #0054AA;
    --brand-mid: #0677BA;
    --brand-soft: #7BADD7;
    --brand-pale: #CADEEF;
    --brand-mist: #E8F1F8;
    --bright: #1e8fff;
    --header-deep: #0b2a8c;
    --header-lite: #1553c9;
    --ink: #2e2e35;
    --row-grey: #e5e6e9;
    --footer: #050608;
    --white: #ffffff;
  }
  * { box-sizing: border-box; margin: 0; padding: 0; }
  html, body { width: 872px; height: 1200px; overflow: hidden; background: #ffffff; }
  .brochure { position: relative; width: 872px; height: 1200px; background: var(--white); font-family: 'Poppins', sans-serif; overflow: hidden; }

  /* Header */
  .hero-band { position: absolute; inset: 0; width: 872px; height: 456px; }
  .brand { position: absolute; left: 49px; top: 74px; display: flex; align-items: center; gap: 10px; }
  .brand-square { width: 30px; height: 30px; background: var(--brand); }
  .brand-name { font-family: 'Poppins', sans-serif; font-weight: 700; font-size: 22px; color: var(--navy); letter-spacing: 0.5px; }

  .hero-photo { position: absolute; left: 421px; top: 47px; width: 451px; height: 387px;
    background: radial-gradient(circle at 62% 38%, #f0c9a0 0%, #6b7fd0 22%, #1c3fb0 48%, #0d2c93 75%),
                linear-gradient(#0d2c93, #0d2c93);
    clip-path: polygon(12% 0, 100% 0, 100% 100%, 8% 100%, 0 85%, 10% 80%); }

  .hero-title { position: absolute; left: 49px; top: 186px; font-family: 'Orbitron', sans-serif; font-weight: 900; font-size: 42px; line-height: 43.5px; color: var(--white); letter-spacing: 1px; }
  .hero-title .accent { color: var(--bright); }
  .hero-sub { position: absolute; left: 50px; top: 332px; border-left: 2px solid var(--white); padding-left: 9px; font-weight: 600; font-size: 13.5px; line-height: 15px; color: var(--white); }
  .hero-intro { position: absolute; left: 49px; top: 383px; width: 380px; font-size: 12px; line-height: 14.6px; color: var(--white); }

  /* Tiers */
  .section-heading { position: absolute; left: 49px; font-family: 'Orbitron', sans-serif; font-weight: 900; color: var(--navy); }
  .tiers-heading { top: 495px; font-size: 17.5px; letter-spacing: 0.3px; }
  .tier-table { position: absolute; left: 49px; top: 526px; width: 775px; border-collapse: collapse; border-radius: 6px; overflow: hidden; box-shadow: 0 1px 4px rgba(0,0,0,0.25); }
  .tier-table th, .tier-table td { text-align: center; font-family: 'Poppins', sans-serif; }
  .tier-table th { height: 42px; width: 120px; font-size: 10.5px; font-weight: 700; color: var(--white); }
  .tier-table th.corner { width: 174px; background: var(--white); }
  .tier-table th:nth-child(even) { background: var(--navy); }
  .tier-table th:nth-child(odd):not(.corner) { background: var(--brand-mid); }
  .tier-table td { height: 39.8px; font-size: 13px; font-weight: 600; color: #222; border-left: 1px solid #d0d2d8; }
  .tier-table .spec { text-align: left; padding-left: 17px; font-family: 'Montserrat', sans-serif; font-weight: 800; font-size: 12.5px; letter-spacing: 3px; color: var(--navy); border-left: none; }
  .tier-table tr:nth-child(odd) td { background: var(--row-grey); }
  .tier-table tr:nth-child(even) td { background: var(--white); }
  .tier-table tr.cost td { background: var(--brand-pale); font-size: 13.5px; font-weight: 700; color: var(--navy); }
  .tier-table tr.cost .spec { color: #111; }

  /* Offer */
  .offer-heading { top: 780px; font-size: 27px; }
  .offer-heading .accent { color: var(--brand); }
  .offer-rule { position: absolute; left: 372px; top: 797px; width: 452px; height: 1px; background: #8a8d95; }
  .offer-list { position: absolute; top: 832px; list-style: none; }
  .offer-list.left { left: 53px; width: 370px; }
  .offer-list.right { left: 438px; width: 390px; }
  .offer-list li { position: relative; padding-left: 16px; font-size: 11.3px; line-height: 14px; color: var(--ink); margin-bottom: 13.4px; }
  .offer-list li svg { position: absolute; left: 0; top: 2px; width: 9px; height: 9px; }

  /* Footer */
  .footer { position: absolute; left: 0; top: 1091px; width: 872px; height: 109px; background: var(--footer); }
  .terms-ribbon { position: absolute; left: 196px; top: 1083px; width: 480px; height: 35px; }
  .terms-text { position: absolute; left: 196px; top: 1083px; width: 480px; height: 35px; display: flex; align-items: center; justify-content: center; font-size: 12px; font-weight: 600; color: var(--white); }
  .contact-call { position: absolute; left: 49px; top: 1128px; font-family: 'Oswald', sans-serif; font-weight: 600; font-size: 26px; color: var(--white); }
  .contact-call .accent { color: var(--bright); }
  .contact-lines { position: absolute; left: 323px; top: 1124px; list-style: none; }
  .contact-lines li { display: flex; align-items: center; gap: 8px; font-size: 14px; line-height: 19px; color: var(--white); }
  .contact-lines svg { width: 10px; height: 10px; }
  .site-box { position: absolute; left: 488px; top: 1136px; width: 390px; height: 26px; border: 1.5px solid var(--brand); border-radius: 3px; padding-left: 15px; display: flex; align-items: center; font-weight: 600; font-size: 19px; letter-spacing: 5px; color: var(--white); }
  .site-box .accent { color: var(--brand-mid); }
</style>
</head>
<body>
<main class="brochure">

  <svg class="hero-band" viewBox="0 0 872 456" aria-hidden="true">
    <defs>
      <linearGradient id="heroBlue" x1="0" y1="0" x2="1" y2="1">
        <stop offset="0" stop-color="#0b2a8c"/>
        <stop offset="1" stop-color="#1553c9"/>
      </linearGradient>
    </defs>
    <polygon points="0,146 347,146 446,47 872,47 872,456 0,456" fill="url(#heroBlue)"/>
    <polygon points="0,140 345,140 444,41 872,41 872,47 446,47 347,146 0,146" fill="#b5b8bf"/>
    <polygon points="0,374 421,374 464,452 0,452" fill="#0a66b8"/>
    <rect x="0" y="451" width="872" height="5" fill="#0a66b8"/>
  </svg>

  <div class="brand">
    <span class="brand-square"></span>
    <span class="brand-name">MERIDANE SYSTEMS</span>
  </div>

  <div class="hero-photo" role="img" aria-label="Photo of a desktop monitor on a desk showing a glowing cloud upload icon over a city skyline at sunset"></div>

  <h1 class="hero-title"><span class="accent">PRIVATE</span><br>CLOUD<br>SERVICES</h1>
  <p class="hero-sub">For our enterprise customers in Perth-based<br>data-centres</p>
  <p class="hero-intro">Meridane Systems is looking to offer private cloud services for our enterprise customers in Perth-based data centres that provides our clients with a lower-cost alternative to Kelvara or QNL yielding better performance.</p>

  <h2 class="section-heading tiers-heading">WE WILL BE PROVIDING FIVE TIERS</h2>
  <table class="tier-table">
    <thead>
      <tr><th class="corner"></th><th>STARTER</th><th>GROWTH</th><th>PROFESSIONAL</th><th>PREMIER</th><th>ELITE</th></tr>
    </thead>
    <tbody>
      <tr><td class="spec">MAX VMS</td><td>5</td><td>10</td><td>15</td><td>20</td><td>25</td></tr>
      <tr><td class="spec">CPU CORES</td><td>8</td><td>16</td><td>32</td><td>48</td><td>64</td></tr>
      <tr><td class="spec">MEMORY</td><td>64</td><td>128</td><td>192</td><td>256</td><td>320</td></tr>
      <tr><td class="spec">SSD STORAGE</td><td>3</td><td>8</td><td>15</td><td>20</td><td>30</td></tr>
      <tr class="cost"><td class="spec">MONTHLY COST</td><td>$ 1,028.01</td><td>$3,426.64</td><td>$4,626.05</td><td>$5,482.72</td><td>$7,196.07</td></tr>
    </tbody>
  </table>

  <h2 class="section-heading offer-heading">WHAT <span class="accent">WE OFFER</span></h2>
  <div class="offer-rule"></div>

  <ul class="offer-list left">
    <li><svg viewBox="0 0 10 10"><circle cx="5" cy="5" r="5" fill="#0677BA"/><path d="M2.6 5.2 4.3 6.8 7.4 3.5" stroke="#fff" stroke-width="1.4" fill="none"/></svg>Hosted in a local Perth-based TIER3 and TIER4 datacentres</li>
    <li><svg viewBox="0 0 10 10"><circle cx="5" cy="5" r="5" fill="#0677BA"/><path d="M2.6 5.2 4.3 6.8 7.4 3.5" stroke="#fff" stroke-width="1.4" fill="none"/></svg>WA owned hosting - support local</li>
    <li><svg viewBox="0 0 10 10"><circle cx="5" cy="5" r="5" fill="#0677BA"/><path d="M2.6 5.2 4.3 6.8 7.4 3.5" stroke="#fff" stroke-width="1.4" fill="none"/></svg>Low latency-ultra fast local hosting</li>
    <li><svg viewBox="0 0 10 10"><circle cx="5" cy="5" r="5" fill="#0677BA"/><path d="M2.6 5.2 4.3 6.8 7.4 3.5" stroke="#fff" stroke-width="1.4" fill="none"/></svg>Includes Orvix Host Datacentre licensing</li>
    <li><svg viewBox="0 0 10 10"><circle cx="5" cy="5" r="5" fill="#0677BA"/><path d="M2.6 5.2 4.3 6.8 7.4 3.5" stroke="#fff" stroke-width="1.4" fill="none"/></svg>Includes BrakWall Managed Firewalls for Enterprise level threat detection</li>
    <li><svg viewBox="0 0 10 10"><circle cx="5" cy="5" r="5" fill="#0677BA"/><path d="M2.6 5.2 4.3 6.8 7.4 3.5" stroke="#fff" stroke-width="1.4" fill="none"/></svg>Includes all infrastructure maintenance services</li>
    <li><svg viewBox="0 0 10 10"><circle cx="5" cy="5" r="5" fill="#0677BA"/><path d="M2.6 5.2 4.3 6.8 7.4 3.5" stroke="#fff" stroke-width="1.4" fill="none"/></svg>Full self management of VMs through customer portal</li>
    <li><svg viewBox="0 0 10 10"><circle cx="5" cy="5" r="5" fill="#0677BA"/><path d="M2.6 5.2 4.3 6.8 7.4 3.5" stroke="#fff" stroke-width="1.4" fill="none"/></svg>Includes a 1gbps Internet link</li>
  </ul>

  <ul class="offer-list right">
    <li><svg viewBox="0 0 10 10"><circle cx="5" cy="5" r="5" fill="#0677BA"/><path d="M2.6 5.2 4.3 6.8 7.4 3.5" stroke="#fff" stroke-width="1.4" fill="none"/></svg>Predictable fixed monthly fee with no dynamic billing</li>
    <li><svg viewBox="0 0 10 10"><circle cx="5" cy="5" r="5" fill="#0677BA"/><path d="M2.6 5.2 4.3 6.8 7.4 3.5" stroke="#fff" stroke-width="1.4" fill="none"/></svg>Highly available cluster, no single point of failure.</li>
    <li><svg viewBox="0 0 10 10"><circle cx="5" cy="5" r="5" fill="#0677BA"/><path d="M2.6 5.2 4.3 6.8 7.4 3.5" stroke="#fff" stroke-width="1.4" fill="none"/></svg>Pricing is based on 36 months commit</li>
    <li><svg viewBox="0 0 10 10"><circle cx="5" cy="5" r="5" fill="#0677BA"/><path d="M2.6 5.2 4.3 6.8 7.4 3.5" stroke="#fff" stroke-width="1.4" fill="none"/></svg>Yearly rate increases capped to a maximum of Australian CPI</li>
    <li><svg viewBox="0 0 10 10"><circle cx="5" cy="5" r="5" fill="#0677BA"/><path d="M2.6 5.2 4.3 6.8 7.4 3.5" stroke="#fff" stroke-width="1.4" fill="none"/></svg>All plans have 24/7/365 support with dedicated after hours number.</li>
    <li><svg viewBox="0 0 10 10"><circle cx="5" cy="5" r="5" fill="#0677BA"/><path d="M2.6 5.2 4.3 6.8 7.4 3.5" stroke="#fff" stroke-width="1.4" fill="none"/></svg>Managed backup and managed disaster recovery services can be added to plans</li>
    <li><svg viewBox="0 0 10 10"><circle cx="5" cy="5" r="5" fill="#0677BA"/><path d="M2.6 5.2 4.3 6.8 7.4 3.5" stroke="#fff" stroke-width="1.4" fill="none"/></svg>No additional charges for Storage Transactions, Internet Usage, VM Snapshots, Datacentre Bandwidth Usage and Firewall Traffic Usage.</li>
  </ul>

  <footer class="footer"></footer>
  <svg class="terms-ribbon" viewBox="0 0 480 35" aria-hidden="true">
    <polygon points="0,8 12,0 468,0 480,8 466,35 14,35" fill="#1b2a7a"/>
    <polygon points="0,8 12,0 14,35" fill="#0b1450"/>
    <polygon points="480,8 468,0 466,35" fill="#0b1450"/>
  </svg>
  <p class="terms-text">SERVICE PROVIDED IN ACCORDANCE WITH OUR TERMS AND CONDITIONS.</p>

  <p class="contact-call">CONTACT US <span class="accent">NOW!</span></p>
  <ul class="contact-lines">
    <li><svg viewBox="0 0 10 10"><circle cx="5" cy="5" r="5" fill="#0677BA"/><path d="M3 2.6c.4 2.2 1.8 3.7 4.2 4.4l.4-1-1.2-.6-.5.5C5 5.5 4.5 5 4.2 4.1l.5-.5L4.1 2.4z" fill="#fff"/></svg>08 6100 4729</li>
    <li><svg viewBox="0 0 10 10"><circle cx="5" cy="5" r="5" fill="#0677BA"/><rect x="2.5" y="3.3" width="5" height="3.6" fill="#fff"/><path d="M2.5 3.3 5 5.3 7.5 3.3" stroke="#0677BA" stroke-width=".7" fill="none"/></svg>info@meridane.com</li>
  </ul>
  <div class="site-box">www.<span class="accent">meridane</span>.com</div>

</main>
</body>
</html>
```